Herbal Apothecary Rebrand

I am in the process of merging two companies Fern Hollow Oils and Under Willow Apothecary. I am dissolving Fern Hollow Oils (FHO) and need to blend a few of the products into the Under Willow Apothecary (UWA) line. These blended products will take on a fresh new look. This is where I need some help. I have a few ideas but need some creative genius to bring them together.
The following products need to be merged and once a logo is agreed upon I will be working with this designer with further pay to create the following:
~ body oils (labels and packaging) **existing product shown in image A-1
~ plant bath medicines (labels and packaging) **a new product with the bottle and packaging shown in images attached
~ facial serum (labels and packaging - the packaging will be the same cardboard boxes used for the body oils) **existing product shown in
image A-2
~ teas (labeling) **a new product - packaging sample pics attached
~ as well as having the ability to carry over into the creation of 40 different essential oil containers. ** An idea I have is shown in image C-1.
Ideas...
I prefer distinct lines, square designs vs circular or curvy. I prefer clean and clear vs busy.
I like the layout shown in images A-1 & A-2 and could see moving forward with a very similar style without the indigenous logo. I would like to see what it looks like to have the UWA logo (building with trees) in place of the indigenous logo. ** I am open to reworking the UWA logo to make it a bit more vertical in size vs being quite small and horizontal. This could include revising or recreating the building and trees altogether.
I like the speckled background (shown in image B-1), it gives the sense that it is aged and goes with the Apothecary theme, however I'm not completely attached to it.
I like the off white labels that I currently have for the BODY OILS and the SERUM and I am leaning towards this as the colour for the new blended line. I would also be open to seeing a lighter version of the turquoise.
This is just an idea that I have however I am open to something completely new. What is important is that it blends nicely with the current line of products available at UWA (the entire line can be seen online). There is a good chance that I will be merging the products over to the new and improved design as we move through the older packaging.
Notes on Plant Bath labels:
**If working from the current layout of the Body Oil labels this can be used as an example to create a template
~ The top will have the new or reworked logo (with or without the company name depending on space available)
~ First line for each bottle will have a name eg: NETTLE + ROSE
~ Second line will be the purpose of the medicine eg: HEART OPENING
~ The next line will read: PLANT BATH
~Then space for a little blurb eg: BRINGING BALANCE TO THE EMOTIONAL AND ENERGETIC HEALTH OF THE HEART.
~ The size of the bottle will read 400 ML but in a vertical direction on the bottle
Notes on Tea labels:
The teas have not been created yet but I'm looking for some ideas that follow in the same design as the Plant Bath labels so the following can be used as an example:
~ Name; TULSI + ROSE
~ The purpose: ELEVATED HEART
~ The bottom will read: LOOSE TEA
~ Blurb about the benefits: A TRANSFORMATIONAL CREATION OF WARM NOTES WITH DEEP WOODY UNDERTONES. THIS ANYTIME TEA IS AS PLEASING IN THE HEALTH BENEFITS AS IT IS TO THE TASTE.
~ Include the size: 100g
**I maxed out in pictures so I wasn't able to add more inspiration pics but I also quite like the brook & meadow tea line (shows up in a google search) as its clean and clear. The difference being I won't be printing directly on the packaging, it will need to be a label.
Logo Text
I would like to see if we can incorporate the name UNDER WILLOW APOTHECARY however this might make it too busy. Perhaps smaller lettering for "under willow" and larger for "APOTHECARY". It also might be the case that adding this on the front makes things look too busy. I'm open to creative suggestions.

```html
<!DOCTYPE html>
<html lang="en">
<head>
<meta charset="utf-8">
<title>Under Willow Apothecary — Label Set</title>
<link href="https://fonts.googleapis.com/css2?family=Oswald:wght@300;400;500&family=Libre+Caslon+Text:wght@400&family=Source+Sans+3:wght@400&display=swap" rel="stylesheet">
<style>
  :root {
    --ink: #6e2a1c;
    --ink-soft: #7d3b2c;
    --paper: #f2f1ee;
    --canvas: #ffffff;
    --speck: rgba(110, 90, 70, 0.10);
    --note: #6b2f22;
  }
  * { box-sizing: border-box; margin: 0; padding: 0; }
  html, body { width: 1200px; height: 1200px; overflow: hidden; background: var(--canvas); }
  .sheet { position: relative; width: 1200px; height: 1200px; }

  .label {
    position: absolute;
    width: 538px; height: 392px;
    background-color: var(--paper);
    background-image:
      radial-gradient(circle at 12% 18%, var(--speck) 0 1px, transparent 1.5px),
      radial-gradient(circle at 63% 72%, var(--speck) 0 1px, transparent 1.5px),
      radial-gradient(circle at 38% 41%, var(--speck) 0 1.2px, transparent 1.8px),
      radial-gradient(circle at 85% 30%, var(--speck) 0 0.8px, transparent 1.3px);
    background-size: 23px 29px, 31px 19px, 41px 37px, 17px 27px;
    color: var(--ink);
    font-family: 'Oswald', sans-serif;
    font-weight: 300;
  }
  .label > * { position: absolute; }
  .label--oil   { left: 44px;  top: 103px; }
  .label--bath  { left: 618px; top: 103px; }
  .label--tea   { left: 44px;  top: 529px; }
  .label--serum { left: 620px; top: 617px; width: 425px; height: 260px; }

  /* side copy, read bottom to top */
  .side-copy {
    left: 26px; top: 44px; height: 322px; width: 58px;
    writing-mode: vertical-rl; transform: rotate(180deg);
    font-size: 9.6px; line-height: 11px; letter-spacing: 0.1px; text-transform: uppercase;
  }
  .side-copy p + p { margin-right: 9px; }
  .side-copy strong { font-weight: 500; }

  .brand-small {
    left: 152px; width: 234px; top: 34px; text-align: center;
    font-family: 'Libre Caslon Text', serif; font-size: 11px; letter-spacing: 3px;
  }
  .brand-main {
    left: 152px; width: 234px; top: 52px; text-align: center;
    font-family: 'Libre Caslon Text', serif; font-size: 21px; letter-spacing: 0.5px;
  }
  .brand-art { left: 158px; top: 98px; width: 208px; height: 72px; }

  .title {
    left: 152px; top: 190px;
    font-weight: 500; font-size: 27px; line-height: 34px; letter-spacing: 0; white-space: nowrap;
  }
  .subtitle {
    left: 152px; top: 238px;
    font-weight: 300; font-size: 24px; line-height: 28px; letter-spacing: 4px; white-space: nowrap;
  }
  .rule { left: 152px; width: 234px; height: 0; border-top: 1.3px solid var(--ink); }
  .rule--a { top: 231px; }
  .rule--b { top: 268px; }
  .rule--c { top: 296px; }
  .rule--d { top: 364px; }
  .botanicals { left: 152px; top: 276px; font-size: 14px; line-height: 18px; letter-spacing: 0.3px; }
  .blurb {
    left: 152px; top: 306px;
    font-size: 13px; line-height: 17px; letter-spacing: 0.3px; text-transform: uppercase; white-space: nowrap;
  }
  .divider { left: 332px; top: 304px; height: 52px; border-left: 1.3px solid var(--ink); }
  .size {
    left: 344px; top: 296px; height: 64px; width: 28px;
    writing-mode: vertical-rl; transform: rotate(180deg);
    font-weight: 400; font-size: 17px; letter-spacing: 1px; text-align: center;
  }
  .panel { left: 434px; top: 36px; width: 79px; height: 328px; border: 1.2px solid var(--ink-soft); }
  .web {
    left: 494px; top: 100px; height: 216px; width: 16px;
    writing-mode: vertical-rl; transform: rotate(180deg);
    font-size: 10.5px; letter-spacing: 0.4px; text-align: center;
  }

  /* per-product adjustments */
  .label--bath .title { top: 182px; font-size: 36px; line-height: 42px; letter-spacing: 1.5px; }
  .label--bath .subtitle { letter-spacing: 4.5px; }
  .label--tea .title { top: 182px; font-size: 38px; line-height: 44px; letter-spacing: 1.8px; }
  .label--tea .subtitle { letter-spacing: 4px; font-size: 25px; }
  .label--tea .divider { left: 349px; }
  .label--tea .size { left: 358px; }

  /* smaller serum label */
  .label--serum .side-copy { left: 30px; top: 30px; height: 210px; width: 60px; font-size: 8.4px; line-height: 10px; }
  .label--serum .side-copy p + p { margin-right: 14px; }
  .label--serum .brand-small { left: 121px; width: 185px; top: 31px; font-size: 9.5px; letter-spacing: 2.5px; }
  .label--serum .brand-main { left: 121px; width: 185px; top: 45px; font-size: 16.5px; }
  .label--serum .title { left: 121px; top: 95px; font-size: 26px; line-height: 32px; letter-spacing: 0; }
  .label--serum .subtitle { left: 121px; top: 148px; font-size: 22px; letter-spacing: 2px; }
  .label--serum .rule { left: 121px; width: 185px; }
  .label--serum .rule--a { top: 136px; }
  .label--serum .rule--b { top: 187px; }
  .label--serum .rule--d { top: 236px; }
  .label--serum .blurb { left: 121px; top: 204px; font-size: 10px; line-height: 13px; letter-spacing: 0.3px; }
  .label--serum .divider { left: 264px; top: 203px; height: 28px; }
  .label--serum .size { left: 276px; top: 198px; height: 40px; width: 22px; font-size: 14px; }
  .label--serum .panel { left: 329px; top: 24px; width: 78px; height: 212px; }
  .label--serum .web { left: 378px; top: 60px; height: 140px; width: 14px; font-size: 8.5px; }

  .spec-notes {
    position: absolute; left: 573px; top: 1045px;
    font-family: 'Source Sans 3', sans-serif; font-size: 21.5px; line-height: 28px; letter-spacing: 0.3px; color: var(--note);
    white-space: nowrap;
  }
</style>
</head>
<body>
<main class="sheet">

  <section class="label label--oil">
    <div class="side-copy">
      <p><strong>Suggested use:</strong> warm oil if desired. Apply to the full body after bathing. Massage in motions toward the heart until the oil is mostly absorbed. Can also be added to bath water.</p>
      <p><strong>Ingredients:</strong> sunflower oil, orange, cardamom, cypress, ginger organic.</p>
    </div>
    <div class="brand-small">UNDER WILLOW</div>
    <div class="brand-main">APOTHECARY</div>
    <svg class="brand-art" role="img" aria-label="Illustration of a small cabin among pine trees" viewBox="0 0 208 72"><rect width="208" height="72" rx="3" fill="#b89489" opacity="0.55"/></svg>
    <h2 class="title">CARDAMON + CYPRESS</h2>
    <div class="rule rule--a"></div>
    <div class="subtitle">WARMING BODY OIL</div>
    <div class="rule rule--b"></div>
    <div class="botanicals">ORGANIC BOTANICALS</div>
    <div class="rule rule--c"></div>
    <p class="blurb">Revitalizing and<br>stimulating for a<br>renewed sense of spirit</p>
    <div class="divider"></div>
    <div class="size">100ML</div>
    <div class="rule rule--d"></div>
    <div class="panel"></div>
    <div class="web">underwillowapothecary.com</div>
  </section>

  <section class="label label--bath">
    <div class="side-copy">
      <p><strong>Suggested use:</strong> warm oil if desired. Apply to the full body after bathing. Massage in motions toward the heart until the oil is mostly absorbed. Can also be added to bath water.</p>
      <p><strong>Ingredients:</strong> sunflower oil, orange, cardamom, cypress, ginger organic.</p>
    </div>
    <div class="brand-small">UNDER WILLOW</div>
    <div class="brand-main">APOTHECARY</div>
    <svg class="brand-art" role="img" aria-label="Illustration of a small cabin among pine trees" viewBox="0 0 208 72"><rect width="208" height="72" rx="3" fill="#b89489" opacity="0.55"/></svg>
    <h2 class="title">NETTLE + ROSE</h2>
    <div class="rule rule--a"></div>
    <div class="subtitle">PLANT BATH</div>
    <div class="rule rule--b"></div>
    <div class="botanicals">ORGANIC BOTANICALS</div>
    <div class="rule rule--c"></div>
    <p class="blurb">Bringing balance to the<br>emotional and energetic<br>health of the heart</p>
    <div class="divider"></div>
    <div class="size">400ML</div>
    <div class="rule rule--d"></div>
    <div class="panel"></div>
    <div class="web">underwillowapothecary.com</div>
  </section>

  <section class="label label--tea">
    <div class="side-copy">
      <p><strong>Suggested use:</strong> warm oil if desired. Apply to the full body after bathing. Massage in motions toward the heart until the oil is mostly absorbed. Can also be added to bath water.</p>
      <p><strong>Ingredients:</strong> sunflower oil, orange, cardamom, cypress, ginger organic.</p>
    </div>
    <div class="brand-small">UNDER WILLOW</div>
    <div class="brand-main">APOTHECARY</div>
    <svg class="brand-art" role="img" aria-label="Illustration of a small cabin among pine trees" viewBox="0 0 208 72"><rect width="208" height="72" rx="3" fill="#b89489" opacity="0.55"/></svg>
    <h2 class="title">TULSI + ROSE</h2>
    <div class="rule rule--a"></div>
    <div class="subtitle">LOOSE TEA</div>
    <div class="rule rule--b"></div>
    <div class="botanicals">ORGANIC BOTANICALS</div>
    <div class="rule rule--c"></div>
    <p class="blurb">A transformational<br>creation of warm notes<br>with deep woody undertones.</p>
    <div class="divider"></div>
    <div class="size">100g</div>
    <div class="rule rule--d"></div>
    <div class="panel"></div>
    <div class="web">underwillowapothecary.com</div>
  </section>

  <section class="label label--serum">
    <div class="side-copy">
      <p>Suggested use: warm oil if desired. Apply to the full body after bathing.</p>
      <p>Ingredients: sunflower oil, orange, cardamom, cypress, ginger organic.</p>
    </div>
    <div class="brand-small">UNDER WILLOW</div>
    <div class="brand-main">APOTHECARY</div>
    <h2 class="title">CAMOMILE + ROSE</h2>
    <div class="rule rule--a"></div>
    <div class="subtitle">BALANCING SERUM</div>
    <div class="rule rule--b"></div>
    <p class="blurb">Botanicals to tame<br>the wild huntress</p>
    <div class="divider"></div>
    <div class="size">35 ML</div>
    <div class="rule rule--d"></div>
    <div class="panel"></div>
    <div class="web">underwillowapothecary.com</div>
  </section>

  <div class="spec-notes">
    <p>Cedarwood + Birch body oil (W x H) 13cm x 9.5cm</p>
    <p>Chamomile + Rose balancing serum (W x H) 10.3cm x 6.3cm</p>
    <p>Plant Baths (W x H) 13cm x 9.5cm</p>
  </div>

</main>
</body>
</html>
```